Accounting firm needing business card / letterhead designed
Marcus L. Trenholm, CPA
marcus@veltrowledger.com
www.veltrowledger.com
842 E Alder Ave Perrysburg, OH 43827
419-562-0974

```html
<!DOCTYPE html>
<html lang="en">
<head>
<meta charset="utf-8">
<title>Veltrow Ledger – Business Card</title>
<link href="https://fonts.googleapis.com/css2?family=Roboto:wght@400;500&family=Roboto+Condensed:wght@500&display=swap" rel="stylesheet">
<style>
  :root {
    --navy: #23205e;
    --green: #8cc63f;
    --paper: #f4f4f4;
    --backdrop: #e4e4e4;
    --ink: #444449;
    --white: #ffffff;
    --muted-white: #e2e2ee;
  }
  * { margin: 0; padding: 0; box-sizing: border-box; }
  html, body {
    width: 1200px; height: 960px; overflow: hidden;
    background: var(--backdrop);
    font-family: "Roboto", Arial, sans-serif;
  }
  .stage { position: relative; width: 1200px; height: 960px; }
  .card {
    position: absolute; width: 600px; height: 342px; overflow: hidden;
  }
  .card--front { left: 314px; top: 113px; background: var(--paper); }
  .card--back { left: 311px; top: 472px; background: var(--navy); }

  .brand-name {
    position: absolute; left: 43px; top: 52px;
    font-family: "Roboto", Arial, sans-serif; font-weight: 500;
    font-size: 40px; letter-spacing: 1px; color: var(--navy);
    text-transform: uppercase; line-height: 1;
  }
  .address, .contacts {
    position: absolute; left: 40px;
    font-size: 14px; line-height: 19px; color: var(--ink);
    list-style: none;
  }
  .address { top: 198px; }
  .contacts { top: 245px; }
  .contacts li { display: flex; align-items: center; gap: 8px; }
  .contacts svg { width: 14px; height: 14px; fill: var(--navy); flex: none; }

  .name-band {
    position: absolute; left: 340px; top: 217px; width: 260px; height: 67px;
    background: var(--navy); display: flex; align-items: center;
    border-left: 18px solid var(--green);
    padding-left: 22px;
  }
  .name-band__text {
    font-family: "Roboto Condensed", Arial, sans-serif; font-weight: 500;
    font-size: 20px; color: var(--white); white-space: nowrap;
  }

  .back-texture {
    position: absolute; inset: 0;
    background: linear-gradient(135deg, #25226a 0%, var(--navy) 50%, #201d57 100%);
  }
  .back-brand {
    position: absolute; left: 0; right: 0; top: 130px; text-align: center;
    font-family: "Roboto", Arial, sans-serif; font-weight: 500;
    font-size: 54px; letter-spacing: 2px; color: var(--white);
    text-transform: uppercase; line-height: 1;
  }
  .back-web {
    position: absolute; left: 0; right: 0; top: 283px; text-align: center;
    font-size: 14px; letter-spacing: 5px; color: var(--muted-white);
  }
</style>
</head>
<body>
<main class="stage">
  <section class="card card--front">
    <div class="brand-name">Veltrow Ledger</div>
    <address class="address">842 E Alder Ave<br>Perrysburg, OH 43827</address>
    <ul class="contacts">
      <li>
        <svg viewBox="0 0 24 24" aria-hidden="true"><path d="M6.6 10.8a15.1 15.1 0 0 0 6.6 6.6l2.2-2.2a1 1 0 0 1 1-.25 11.4 11.4 0 0 0 3.6.57 1 1 0 0 1 1 1V20a1 1 0 0 1-1 1A17 17 0 0 1 3 4a1 1 0 0 1 1-1h3.5a1 1 0 0 1 1 1c0 1.25.2 2.46.57 3.6a1 1 0 0 1-.25 1z"/></svg>
        419-562-0974
      </li>
      <li>
        <svg viewBox="0 0 24 24" aria-hidden="true"><path d="M2 5h20v14H2z M2 6l10 7 10-7" fill="none" stroke="#23205e" stroke-width="0"/><path d="M2 5h20v2l-10 7L2 7z M2 9l10 7 10-7v10H2z"/></svg>
        marcus@veltrowledger.com
      </li>
      <li>
        <svg viewBox="0 0 24 24" aria-hidden="true"><circle cx="12" cy="12" r="10"/><path d="M7 8c2 0 3 1 3 3s-2 2-2 4 2 3 2 5M14 4c0 2 2 2 3 4s-1 3 0 5 3 1 3 1" fill="none" stroke="#f4f4f4" stroke-width="1.6"/></svg>
        www.veltrowledger.com
      </li>
    </ul>
    <div class="name-band"><span class="name-band__text">Marcus L. Trenholm, CPA</span></div>
  </section>

  <section class="card card--back">
    <div class="back-texture" role="img" aria-label="Faint repeating brand-name pattern on navy background"></div>
    <div class="back-brand">Veltrow Ledger</div>
    <div class="back-web">www.veltrowledger.com</div>
  </section>
</main>
</body>
</html>
```